Lantern Petals Website v.1 - attract floral shop franchisees

I need a simple information website for my new business. We are a franchisor of flower shops. The overall purpose of the website is to promote the company and the service, especially to potential franchisees and retailers. Only about 4 pages are required including homepage, About, For Supermarkets, For Franchisees, and Contact. No special functions are required except the site will have two separate inquiry forms that must be filled out online and submitted via automated email. Similarly, an email form should be linked from the Contact page. I have a logo and business cards designed by ArtMingle, and I would like the site to have a consistent color scheme and style. The key to design will be to express the joy and love associated with flowers and floral bouquets.
IMPORTANT - I will be exporting the website design to Wordpress CMS in a site hosted by HostNimbus. For smooth integration into WordPress hosted by HostNimbus, the designer should build the site using a WordPress-friendly format. Ideally, they should use HTML, CSS, and PHP. Creating a custom theme or using a page builder that exports to WordPress-compatible files is best. This ensures the site can be easily imported and managed within WordPress.

Target Market(s)

Potential franchisees (existing florists or creative types who might like to own a floral business) and supermarkets who might want us to run their floral department

Industry/Entity Type

Floral retailing

Requirements
Must have
• A brand theme that is beautiful, consistent throughout and builds on the logo design
Nice to have
• Show gender and ethnic diversity in customers and florists. Pictures of happy florists (for franchisees) and pictures of amazing floral department displays (for supermarkets)

```html
<!DOCTYPE html>
<html lang="en">
<head>
<meta charset="utf-8">
<title>Lantern Petals</title>
<link href="https://fonts.googleapis.com/css2?family=Arimo:wght@400;700&family=Great+Vibes&display=swap" rel="stylesheet">
<style>
:root{
  --green:#169447;
  --green-deep:#0d7a38;
  --amber:#f2ae2e;
  --amber-soft:#f6c45a;
  --cream:#f3f2e4;
  --ink:#2a2a2a;
  --muted:#444;
  --night:#1b1d1c;
  --white:#fff;
}
*{box-sizing:border-box;margin:0;padding:0}
html,body{width:1200px;height:3331px;overflow:hidden}
body{position:relative;background:var(--white);font-family:"Arimo",Arial,sans-serif;color:var(--ink)}
.abs{position:absolute}
.script{font-family:"Great Vibes",cursive;color:var(--amber);font-size:26px;display:flex;align-items:center;gap:8px}
.script::after{content:"";width:62px;height:1px;background:var(--amber)}
.btn{position:absolute;display:flex;align-items:center;justify-content:center;background:var(--amber);color:var(--white);border-radius:18px;font-size:12px}
.photo{position:absolute;border-radius:50%}
.para{font-size:10.3px;line-height:15px;color:var(--muted)}

/* hero */
.hero{position:absolute;left:0;top:0;width:1200px;height:660px;background:radial-gradient(ellipse at 78% 30%,#c8901c 0%,#7a5314 22%,#2d2a1e 48%,#1b2124 75%);}
.brand{position:absolute;left:123px;top:22px;display:flex;align-items:center;gap:8px;color:var(--amber);font-size:24px}
.brand .dot{width:26px;height:26px;border-radius:50%;border:2px solid var(--amber)}
.search{position:absolute;left:851px;top:26px;width:177px;height:32px;border:1px solid #ddd;border-radius:16px;color:#eee;font-size:11px;padding:9px 12px}
.search svg{position:absolute;right:10px;top:9px}
.menu{position:absolute;left:1054px;top:32px}
.hero h1{position:absolute;left:123px;top:350px;width:345px;color:var(--white);font-weight:400;font-size:41px;line-height:45px}
.hero .lede{position:absolute;left:123px;top:498px;width:290px;color:var(--white);font-size:12.5px;line-height:17px}

/* split sections */
.split-text h2{font-weight:400;font-size:28px;color:var(--ink);margin:2px 0 12px}
.ring{position:absolute;border-radius:50%}
.bee{position:absolute;width:26px;height:26px;border-radius:50%;background:var(--amber)}
.trail{position:absolute;width:80px;height:200px;border-radius:40px;background:rgba(22,148,71,.06)}
.ghost{position:absolute;background:#ececec;border-radius:40% 40% 10% 10%}

.markets{position:absolute;left:0;top:1134px;width:1200px;height:534px;background:linear-gradient(180deg,#138a44,#0c6f34 60%,#15803d)}
.markets h2{color:var(--white)}
.markets .para{color:var(--white)}

/* gallery */
.gallery{position:absolute;left:0;top:2105px;width:1200px;height:640px;background:var(--cream)}
.g-title{position:absolute;left:0;width:1200px;text-align:center}
.g-script{position:absolute;left:0;width:1200px;top:30px;display:flex;justify-content:center;align-items:center;gap:8px;font-family:"Great Vibes",cursive;color:var(--amber);font-size:24px}
.g-script::before,.g-script::after{content:"";width:62px;height:1px;background:var(--amber)}
.tile{position:absolute}

/* cta */
.cta{position:absolute;left:0;top:2728px;width:1200px;height:373px;background:linear-gradient(180deg,#f6b52a,#f3a81f 60%,#f7c540)}
.cta h3{position:absolute;left:0;width:1200px;top:200px;text-align:center;color:var(--white);font-weight:400;font-size:27px}
.signup{position:absolute;left:343px;top:240px;width:513px;height:39px;background:var(--white);border-radius:20px;border:2px solid #fff;font-size:11px;padding:12px 15px}
.signup span.go{position:absolute;right:2px;top:2px;width:122px;height:31px;border-radius:16px;background:var(--green);color:#fff;display:flex;align-items:center;justify-content:center;font-size:12px}

/* footer */
.footer{position:absolute;left:0;top:3101px;width:1200px;height:230px;background:var(--night);color:#eee}
.footer h4{font-weight:400;font-size:17px;margin-bottom:14px}
.footer .col{position:absolute;top:30px}
.footer .rule{position:absolute;top:30px;width:1px;height:158px;background:#666}
.footer p,.footer li{font-size:9.5px;line-height:14.5px}
.footer ul{list-style:none}
.footer li{line-height:19.5px}
.contact-row{display:flex;align-items:center;gap:8px;font-size:9.5px;margin-bottom:12px}
.contact-row i{width:22px;height:22px;border-radius:50%;border:1px solid #ddd;display:flex;align-items:center;justify-content:center}
.copyright{position:absolute;left:122px;top:187px;width:956px;border-top:1px solid #777;text-align:center;font-size:9px;padding-top:14px}
</style>
</head>
<body>

<!-- Hero -->
<header class="hero" role="img" aria-label="Close-up of a sunflower with a bee in flight against a dark glowing background">
  <div class="brand"><span class="dot"></span>Lantern Petals</div>
  <div class="search">Search
    <svg width="12" height="12" viewBox="0 0 12 12"><circle cx="5" cy="5" r="4" fill="none" stroke="#fff" stroke-width="1.4"/><line x1="8" y1="8" x2="11" y2="11" stroke="#fff" stroke-width="1.4"/></svg>
  </div>
  <svg class="menu" width="24" height="18" viewBox="0 0 24 18"><g stroke="#fff" stroke-width="2" stroke-linecap="round"><line x1="6" y1="2" x2="22" y2="2"/><line x1="2" y1="9" x2="22" y2="9"/><line x1="10" y1="16" x2="22" y2="16"/></g></svg>
  <div class="script abs" style="left:122px;top:312px">Welcome to Lantern Petals</div>
  <h1>Lantern Petals is an entrepreneurial Company</h1>
  <p class="lede">Created to make top quality fresh flowers and artisan-designed bouquets accessible to every consumer at affordable prices.</p>
  <svg class="abs" style="left:0;top:0" width="1200" height="660" viewBox="0 0 1200 660">
    <path d="M280,660 C620,650 860,430 1200,412 L1200,660 Z" fill="var(--amber)"/>
    <path d="M820,590 C960,540 1110,535 1200,570 L1200,605 C1110,580 960,570 820,590 Z" fill="var(--green)"/>
    <path d="M0,537 C140,600 280,650 420,652 C700,650 900,560 1200,605 L1200,660 L0,660 Z" fill="var(--white)"/>
  </svg>
</header>

<!-- About -->
<section class="about">
  <div class="ghost" style="left:0;top:860px;width:110px;height:250px;opacity:.6" role="img" aria-label="Faint honeycomb flower decoration"></div>
  <div class="ring" style="left:170px;top:718px;width:378px;height:378px;background:var(--green)"></div>
  <div class="photo" style="left:194px;top:730px;width:350px;height:350px;background:linear-gradient(135deg,#8a9aa0,#c9b37a 45%,#e0c93a 70%,#4a4f3a)" role="img" aria-label="Smiling florist holding an armful of yellow chrysanthemums in a greenhouse"></div>
  <div class="ring" style="left:393px;top:856px;width:208px;height:208px;background:var(--amber)"></div>
  <div class="photo" style="left:405px;top:866px;width:194px;height:194px;border:5px solid #fff;background:radial-gradient(circle,#e2508a,#b8324f 50%,#5b4a3a)" role="img" aria-label="Bouquet of pink and red roses in a vase"></div>
  <div class="trail" style="left:640px;top:810px" role="img" aria-label="Bee flight trail decoration"></div>
  <div class="bee" style="left:672px;top:790px" role="img" aria-label="Bee mascot"></div>
  <div class="split-text abs" style="left:733px;top:755px;width:345px">
    <div class="script">About Us</div>
    <h2>About Lantern Petals</h2>
    <p class="para">Fresh flowers convey special sentiments - love, happiness, joy – which every person deserves. Lantern Petals is an entrepreneurial company created to make top quality fresh flowers and artisan-designed bouquets accessible to every consumer at affordable prices.</p>
    <p class="para" style="margin-top:14px">Lantern Petals brings the best of professional florists and supermarkets together for the benefit of consumers. It supports a national network of franchisees who own and operate the floral departments of some of the country's most progressive supermarkets, selling the finest floral stems and bouquets to customers at the market's best value.</p>
  </div>
  <div class="btn" style="left:733px;top:993px;width:107px;height:35px">More About Us</div>
</section>

<!-- Supermarkets -->
<section class="markets" role="img" aria-label="Rows of plants growing inside a green greenhouse">
  <div class="split-text abs" style="left:122px;top:43px;width:390px">
    <div class="script">Supermarkets</div>
    <h2>For Supermarkets</h2>
    <p class="para">Supermarket flower departments benefit from high customer footfall, economies of scale and low pricing. However their quality of stems and bouquets is often poor and in-store service is limited. In contrast, professional florists typically sell the finest quality stems, design the most beautiful bouquets and provide the finest customer service, but their costs and customer prices are high. Supermarkets find that Lantern Petals, through their florist franchise network, is able to improve their financial outcomes, provide attentive customer service and satisfaction, and lift the quality of the entire store environment.</p>
  </div>
  <div class="btn" style="left:122px;top:249px;width:157px;height:34px">More For Supermarkets</div>
  <svg class="abs" style="left:0;top:0" width="1200" height="534" viewBox="0 0 1200 534">
    <path d="M0,290 C200,290 320,330 520,430 C680,510 900,520 1200,450 L1200,534 L0,534 Z" fill="var(--amber)"/>
    <path d="M0,480 C100,440 260,440 380,470 C250,470 120,500 0,520 Z" fill="var(--green)"/>
    <path d="M0,534 L0,520 C120,500 250,470 380,470 C560,500 700,534 850,534 Z" fill="var(--white)"/>
    <path d="M640,534 C900,520 1080,480 1200,420 L1200,534 Z" fill="var(--white)"/>
  </svg>
  <div class="ring" style="left:655px;top:50px;width:380px;height:380px;background:var(--amber)"></div>
  <div class="photo" style="left:663px;top:57px;width:346px;height:346px;background:linear-gradient(135deg,#d84a62,#6a9a4a 40%,#9db6c8 70%,#3a4a3a)" role="img" aria-label="Smiling florist carrying potted geraniums in a greenhouse"></div>
  <div class="ring" style="left:571px;top:193px;width:212px;height:212px;background:var(--green-deep)"></div>
  <div class="photo" style="left:578px;top:200px;width:198px;height:198px;border:5px solid #fff;background:radial-gradient(circle,#f0a030,#d06030 45%,#4a3a2a)" role="img" aria-label="Supermarket display of orange and yellow protea bouquets"></div>
</section>

<!-- Franchisees -->
<section class="franchise">
  <div class="ghost" style="left:0;top:1840px;width:110px;height:250px;opacity:.6" role="img" aria-label="Faint honeycomb flower decoration"></div>
  <div class="ring" style="left:160px;top:1677px;width:390px;height:370px;background:var(--green)"></div>
  <div class="photo" style="left:185px;top:1680px;width:362px;height:362px;background:linear-gradient(135deg,#c9d0d6,#5a78a0 40%,#e6b8b8 65%,#8a8a8a)" role="img" aria-label="Smiling male florist in an apron holding a rose bouquet in a glass vase"></div>
  <div class="ring" style="left:388px;top:1816px;width:208px;height:208px;background:var(--amber)"></div>
  <div class="photo" style="left:397px;top:1826px;width:194px;height:194px;border:5px solid #fff;background:radial-gradient(circle,#f4c020,#e07a6a 45%,#6a7a3a)" role="img" aria-label="Bouquet of sunflowers and pink roses"></div>
  <div class="trail" style="left:622px;top:1800px" role="img" aria-label="Bee flight trail decoration"></div>
  <div class="bee" style="left:655px;top:1780px" role="img" aria-label="Bee mascot"></div>
  <div class="split-text abs" style="left:715px;top:1745px;width:360px">
    <div class="script">Franchisees</div>
    <h2>For Franchisees</h2>
    <p class="para">Lantern Petals supports a national network of owner-operator franchisees with comprehensive services to enhance franchise profits. Our franchisees are the cornerstone of our business. Many of them are already professional florists or florist employees who wish to expand their businesses without the significant costs of a traditional flower shop. Others are creative types or flower lovers who have made a career change in order to express their talents and make people happy. Still others are entrepreneurs in search of owning their own business. All are welcome if they meet Lantern Petals' high standards of quality, service and ethical Business practices.</p>
  </div>
  <div class="btn" style="left:715px;top:1985px;width:143px;height:34px">More For Franchisees</div>
</section>

<!-- Gallery -->
<section class="gallery">
  <div class="g-script">Our Gallery</div>
  <h2 class="g-title" style="top:63px;font-weight:400;font-size:28px">Our Gallery</h2>
  <div class="tile" style="left:122px;top:122px;width:279px;height:194px;background:linear-gradient(135deg,#5a4a3a,#c8a080 50%,#e08060)" role="img" aria-label="Florist arranging flowers in a shop"></div>
  <div class="tile" style="left:412px;top:122px;width:278px;height:194px;background:linear-gradient(135deg,#e04a70,#f0d040 50%,#c070c0)" role="img" aria-label="Buckets of colourful flowers at a market stall"></div>
  <div class="tile" style="left:702px;top:122px;width:375px;height:402px;background:linear-gradient(160deg,#8a6a3a,#e0d8b8 35%,#4a70c0 60%,#d8a8a0)" role="img" aria-label="Woman holding a basket of blue hydrangeas"></div>
  <div class="tile" style="left:122px;top:329px;width:279px;height:192px;background:linear-gradient(135deg,#e8e8e8,#9a70c0 40%,#e8c830 65%,#5a8040)" role="img" aria-label="Tulips and yellow mimosa in vases outdoors"></div>
  <div class="tile" style="left:412px;top:329px;width:278px;height:192px;background:linear-gradient(135deg,#c02030,#e07050 50%,#f08a50)" role="img" aria-label="Gloved hands arranging red and orange roses"></div>
  <div class="btn" style="left:538px;top:552px;width:124px;height:33px">More Our Gallery</div>
</section>

<!-- Call to action -->
<section class="cta" role="img" aria-label="Warm yellow flower field background">
  <svg class="abs" style="left:0;top:0" width="1200" height="373" viewBox="0 0 1200 373">
    <path d="M0,0 L1200,0 L1200,95 C1000,40 800,-20 290,10 L0,10 Z" fill="var(--cream)"/>
    <path d="M290,10 C650,-20 800,90 950,160 C1050,205 1130,215 1200,205 L1200,260 C1100,270 1000,230 900,180 C750,100 600,30 290,10 Z" fill="var(--green)"/>
    <path d="M820,65 C950,90 1100,140 1200,100 L1200,130 C1100,150 960,110 820,65 Z" fill="var(--amber-soft)"/>
  </svg>
  <div class="abs" style="left:80px;top:60px;width:190px;height:310px;border-radius:45% 45% 10% 10%;background:rgba(255,255,255,.35)" role="img" aria-label="Honeycomb flower emblem decoration"></div>
  <h3>Start Your New Journey Lantern Petals</h3>
  <div class="signup">Enter Your Email<span class="go">More Our Gallery</span></div>
</section>

<!-- Footer -->
<footer class="footer">
  <div class="abs" style="left:123px;top:62px;display:flex;align-items:center;gap:10px;color:var(--amber);font-size:28px"><span style="width:34px;height:34px;border-radius:50%;border:2px solid var(--amber)"></span>Lantern Petals</div>
  <span class="rule" style="left:363px"></span>
  <div class="col" style="left:410px;width:210px">
    <h4>About Us</h4>
    <p>Fresh flowers convey special sentiments - love, happiness, joy – which every person deserves. Lantern Petals is an entrepreneurial company created to make top quality fresh flowers and artisan-designed bouquets accessible to every consumer at affordable prices.</p>
  </div>
  <span class="rule" style="left:653px"></span>
  <div class="col" style="left:724px">
    <h4>Quick Link</h4>
    <ul><li>Home</li><li>About Us</li><li>For Supermarkets</li><li>For Franchisees</li><li>Our Gallery</li><li>Contact Us</li></ul>
  </div>
  <span class="rule" style="left:878px"></span>
  <div class="col" style="left:937px">
    <h4>Contact Us</h4>
    <div class="contact-row"><i><svg width="10" height="8" viewBox="0 0 10 8"><rect x=".5" y=".5" width="9" height="7" fill="none" stroke="#fff"/><path d="M.5,.5 L5,4.5 L9.5,.5" fill="none" stroke="#fff"/></svg></i>hello@lantern-petals.example</div>
    <div class="contact-row"><i><svg width="10" height="10" viewBox="0 0 10 10"><path d="M2,1 L4,3 L3,4 C4,6 5,7 6,7 L7,6 L9,8 L8,9.5 C4,9 1,6 .5,2 Z" fill="#fff"/></svg></i>+1.555.010.2048</div>
  </div>
  <div class="copyright">Copyright © 2024 Lantern Petals All Rights Reserved.</div>
</footer>

</body>
</html>
```